Business Card Design - Photographer

I am a landscape photographer and I require a business card design. 

I require two designs:
1)  a double sided business card
 and
b)  a single sided business card 

The single sided design can either be the same as the double sided (with just one side having all the information)....or it can be an entire new design. Its up to you.

My corporate colours are (CMYK):

Blue   69, 32, 0, 0
Grey  72,  64,  47,  31
Green  32,  2,  91,  0
Yellow   0, 19, 92, 0
Orange  0, 39, 75, 0

Colour space in final file should be in CMYK.

The details that need to be included on the card:

- Use the provided Logo
- Name: Wiktor Baranowski
- Email:   sales@vistalumeworks.com.au
- Website:    vistalumeworks.com.au
- Twitter:    twitter.com/vistalumeworks
- Facebook:   facebook.com/vistalumeworks
- Mobile  0417 539 662

Please use the attached template to design the logo to the specified size, including the marked bleed lines. I have also attached my logo in PNG (transparent background) and ai format for you to use.

The final file should be:
- Photoshop version with layers so I can edit the name/text etc. All non vector files should be high resolution at 1039 x 697 pixels at 300 dpi.

I also require a file as:
- Vector based PDF

Anyway questions please contact me.

Thank you

Industry/Entity Type

Landscape

Logo styles of interest
Pictorial/Combination Logo
Abstract Logo
Wordmark Logo
Lettermark Logo
Requirements
Must have
• The details that need to be included on the card:

- Use the provided Logo
- Name: Wiktor Baranowski
- Email: sales@vistalumeworks.com.au
- Website: vistalumeworks.com.au
- Twitter: twitter.com/vistalumeworks
- Facebook: facebook.com/vistalumeworks
- Mobile 0417 539 662

```html
<!DOCTYPE html>
<html lang="en">
<head>
<meta charset="utf-8">
<title>Wiktor Baranowski – Business Card</title>
<link href="https://fonts.googleapis.com/css2?family=Cinzel:wght@400;600;700&display=swap" rel="stylesheet">
<style>
  :root {
    --backdrop: #818285;
    --card-white: #ffffff;
    --brand-blue: #3d90d0;
    --brand-green: #b9d33f;
    --brand-grey: #3c3e50;
    --text-grey: #4a4b58;
  }
  * { margin: 0; padding: 0; box-sizing: border-box; }
  html, body {
    width: 1200px;
    height: 736px;
    overflow: hidden;
    background: var(--backdrop);
  }
  .card {
    position: absolute;
    left: 142px;
    top: 110px;
    width: 938px;
    height: 535px;
    border-radius: 40px;
    overflow: hidden;
    background: var(--card-white);
    box-shadow: 3px 4px 8px rgba(0,0,0,0.35);
    font-family: "Cinzel", "Times New Roman", serif;
    color: var(--text-grey);
  }
  .card__swoosh {
    position: absolute;
    inset: 0;
  }
  .card__mobile {
    position: absolute;
    left: 700px;
    top: 67px;
    font-size: 22px;
    letter-spacing: 0.6px;
  }
  .brand__mark {
    position: absolute;
    left: 183px;
    top: 65px;
    width: 168px;
    height: 168px;
    border-radius: 50%;
    background: var(--brand-grey);
  }
  .brand__name {
    position: absolute;
    left: 41px;
    top: 252px;
    width: 450px;
    text-align: center;
    font-size: 36px;
    font-weight: 600;
    letter-spacing: 0.5px;
    color: var(--brand-grey);
    white-space: nowrap;
  }
  .brand__rule {
    position: absolute;
    left: 41px;
    top: 301px;
    width: 450px;
    height: 2px;
    background: var(--brand-grey);
  }
  .brand__tagline {
    position: absolute;
    left: 41px;
    top: 313px;
    width: 450px;
    text-align: center;
    font-size: 16px;
    font-weight: 700;
    letter-spacing: 3.4px;
    color: var(--brand-grey);
    white-space: nowrap;
  }
  .contact {
    position: absolute;
    left: 63px;
    top: 365px;
    list-style: none;
    font-size: 20px;
    line-height: 31px;
    letter-spacing: 0.6px;
    white-space: nowrap;
  }
  .contact__key {
    color: var(--brand-blue);
    font-size: 22px;
  }
  .card__web {
    position: absolute;
    left: 53px;
    top: 476px;
    font-size: 21px;
    font-weight: 600;
    color: var(--brand-grey);
    letter-spacing: 0.6px;
    white-space: nowrap;
  }
  .card__web-domain {
    font-size: 26px;
  }
</style>
</head>
<body>
  <div class="card">
    <svg class="card__swoosh" width="938" height="535" viewBox="0 0 938 535" aria-hidden="true">
      <rect class="swoosh__green" x="0" y="0" width="938" height="535" fill="var(--brand-green)"/>
      <path class="swoosh__blue" d="M0,0 L303,0 C620,95 860,290 920,535 L0,535 Z" fill="var(--brand-blue)"/>
      <path class="swoosh__white" d="M0,0 L298,0 C580,85 780,290 813,535 L0,535 Z" fill="var(--card-white)"/>
    </svg>

    <div class="card__mobile">M : 0417 539 662</div>

    <div class="brand__mark"></div>
    <div class="brand__name">WIKTOR BARANOWSKI</div>
    <div class="brand__rule"></div>
    <div class="brand__tagline">FINE ART PHOTOGRAPHY</div>

    <ul class="contact">
      <li><span class="contact__key">E</span> : sales@vistalumeworks.com.au</li>
      <li><span class="contact__key">T</span> : twitter.com/vistalumeworks</li>
      <li><span class="contact__key">F</span> : facebook.com/vistalumeworks</li>
    </ul>

    <div class="card__web">www.<span class="card__web-domain">VISTALUMEWORKS</span>.com.au</div>
  </div>
</body>
</html>
```